Design a book cover
TItle: Where Would Mercy Stand?
Suggested graphic: Jesus holding a gun
Subtitle: A public defender's views on the death penalty
Author Name: Gordon Maskelyne

```html
<!DOCTYPE html>
<html lang="en">
<head>
<meta charset="utf-8">
<title>Where Would Mercy Stand? — Gordon Maskelyne</title>
<link rel="stylesheet" href="https://fonts.googleapis.com/css2?family=Playfair+Display:wght@900&family=Montserrat:wght@300&family=Bebas+Neue&display=swap">
<style>
  :root {
    --paper: #f5eedf;
    --ink: #0b0b0b;
    --blood: #b01917;
    --sketch-fill: #e8dfcc;
  }
  html, body {
    margin: 0;
    padding: 0;
    overflow: hidden;
    background: var(--paper);
  }
  .cover {
    position: relative;
    width: 800px;
    height: 1200px;
    background: var(--paper);
    overflow: hidden;
  }
  .subtitle-rule {
    position: absolute;
    left: 216px;
    top: 150px;
    width: 2px;
    height: 178px;
    background: var(--ink);
  }
  .subtitle {
    position: absolute;
    left: 238px;
    top: 146px;
    margin: 0;
    font-family: "Montserrat", sans-serif;
    font-weight: 300;
    font-size: 29.5px;
    line-height: 37px;
    letter-spacing: 0.02em;
    color: var(--ink);
  }
  .cover-art {
    position: absolute;
    left: 467px;
    top: 94px;
    width: 158px;
    height: 319px;
    background: linear-gradient(180deg, var(--sketch-fill) 0%, #efe6d4 100%);
    border-radius: 40px 40px 60px 60px;
  }
  .type {
    position: absolute;
    left: 0;
    top: 0;
    width: 800px;
    height: 1200px;
  }
  .title-red { fill: var(--blood); font-family: "Playfair Display", serif; font-weight: 900; }
  .title-black { fill: var(--ink); font-family: "Playfair Display", serif; font-weight: 900; }
  .author { fill: var(--ink); font-family: "Bebas Neue", sans-serif; }
</style>
</head>
<body>
<main class="cover">
  <span class="subtitle-rule"></span>
  <p class="subtitle">A public<br>defender’s<br>views on<br>the death<br>penalty</p>

  <div class="cover-art" role="img" aria-label="Line illustration of a hand gripping a revolver aimed straight at the viewer"></div>

  <svg class="type" viewBox="0 0 800 1200" aria-labelledby="book-title">
    <title id="book-title">Where Would Mercy Stand? by Gordon Maskelyne</title>
    <text class="title-red" x="172" y="542" font-size="150" textLength="453" lengthAdjust="spacingAndGlyphs">Where</text>
    <text class="title-red" x="226" y="666" font-size="126" textLength="397" lengthAdjust="spacingAndGlyphs">Would</text>
    <text class="title-black" x="100" y="801" font-size="178" textLength="538" lengthAdjust="spacingAndGlyphs">Mercy</text>
    <text class="title-black" x="176" y="944" font-size="164" textLength="521" lengthAdjust="spacingAndGlyphs">Stand?</text>
    <text class="author" x="171" y="1095" font-size="61" textLength="449" lengthAdjust="spacing">GORDON MASKELYNE</text>
  </svg>
</main>
</body>
</html>
```